BrivoNest Learning App for Children with Dyslexia

Project Description:

We are seeking a talented UI/UX designer to create engaging and intuitive designs for Brivonest, an innovative educational app designed to help children learn letters and words through a multisensory learning approach. The app aims to be particularly helpful for children with dyslexia, providing a supportive and interactive learning environment.

Key App Features & Design Requirements:

Account Creation Screen: Design a welcoming and straightforward sign-up page that allows users to register with their email or continue with Quarnix. The design should be clean, focusing on user-friendliness and accessibility, adhering to our terms of service and privacy policy.

Main Screen Design: The main screen should allocate at least 4/6 of its height to the interactive drawing area. It needs to display word prompts in both correct and scrambled orders and include options to "Show all Words," "Play all words," and a search function. The interface should be vibrant, engaging, and easy to navigate for children.

Profile Section: Create a user-friendly profile page that allows users to edit their profile image, name, username, email, links, and bio. The design should be clean and encourage user engagement.

BrivoTally Page: This section will display the user's learning progress, including rankings, a learning curve, and recently learned words. It should visually represent progress in a motivating and understandable way, suitable for a younger audience.

Visual and Auditory Feedback Implementation: Incorporate elements that support visual and auditory feedback, using dyslexia-friendly formats. This includes choosing appropriate colors, fonts, and auditory cues.

Accessibility and Customization Settings: Designs should include settings for adjusting visual contrast, font size, and the word list to accommodate individual preferences and needs.

Feel free to add more interactions and/or pages.

Design preferences:

Color Scheme: Use a bright, inviting color palette that stimulates learning and engagement without overwhelming the users.
Font Selection: Opt for fonts that are readable and accessible, particularly for users with dyslexia.
Icons and Graphics: Design custom icons and graphics that are cohesive with the app's theme and purpose. Illustrations should be simple, relatable, and supportive of the learning process.

Target Market(s)

Educational

Industry/Entity Type

Educational

Colors
0054AA
0677BA
7BADD7
CADEEF
E8F1F8
0094D4
00A9DD
6FCCEA
C7EBF8
E9F6FB

Requirements
Must have
• Educational app, a writing area, scoring and account management
Nice to have
• Statistics, Ranking Page, Settings and some nice visual features

```html
<!DOCTYPE html>
<html lang="en">
<head>
<meta charset="utf-8">
<title>Brivonest – App Screens</title>
<link href="https://fonts.googleapis.com/css2?family=Roboto:wght@400;500;700&display=swap" rel="stylesheet">
<style>
  :root{
    --navy:#0054AA;
    --ocean:#0677BA;
    --sky:#7BADD7;
    --mist:#CADEEF;
    --ice:#E8F1F8;
    --pale:#E9F6FB;
    --ink:#1b1b1b;
    --muted:#6b6b6b;
    --line:#cfcfcf;
    --paper:#ffffff;
    --stage:#ffffff;
    --profile-bg:#ececec;
    --avatar-ring:#3aa55a;
  }
  *{box-sizing:border-box;margin:0;padding:0}
  html,body{width:1200px;height:542px;overflow:hidden;background:var(--stage)}
  body{font-family:'Roboto',sans-serif;color:var(--ink);position:relative}
  .screen{position:absolute;top:28px;width:250px;height:486px;background:var(--paper);
    box-shadow:0 4px 18px rgba(0,0,0,.08);overflow:hidden}
  .screen--signup{left:165px}
  .screen--profile{left:475px;background:var(--profile-bg)}
  .screen--main{left:785px}
  .abs{position:absolute}

  /* Sign up */
  .brand{top:14px;left:0;width:100%;text-align:center}
  .brand__name{font-size:20px;font-weight:500;letter-spacing:.2px}
  .brand__tag{font-size:6.5px;color:#333;margin-top:1px}
  .hero{top:64px;left:37px;width:176px;height:134px;border-radius:10px;
    background:linear-gradient(135deg,#fde3c8,#cfe6c4 50%,#c9dcf2)}
  .signup__title{top:220px;width:100%;text-align:center;font-size:12px;font-weight:500}
  .signup__lead{top:245px;width:100%;text-align:center;font-size:8px;color:#222}
  .field{top:270px;left:26px;width:197px;height:24px;border:1px solid var(--line);
    font-size:7px;color:#555;padding:0 8px;display:flex;align-items:center;justify-content:space-between}
  .btn-primary{top:308px;left:26px;width:197px;height:24px;background:var(--navy);color:#fff;
    font-size:8.5px;font-weight:500;display:flex;align-items:center;justify-content:center}
  .divider{top:350px;left:28px;width:193px;display:flex;align-items:center;gap:6px;font-size:7px;color:#555}
  .divider::before,.divider::after{content:"";flex:1;height:1px;background:#999}
  .btn-soft{top:379px;left:26px;width:197px;height:23px;background:var(--ice);
    font-size:8.5px;font-weight:500;display:flex;align-items:center;justify-content:center;gap:5px}
  .dot{width:8px;height:8px;border-radius:50%;background:var(--ocean)}
  .legal{top:422px;width:100%;text-align:center;font-size:7.3px;color:#555;line-height:15px}
  .legal b{color:#111;font-weight:500}

  /* Profile */
  .back{top:22px;left:13px;width:20px;height:16px;background:#fff;display:flex;align-items:center;justify-content:center}
  .screen-title{top:20px;width:100%;text-align:center;font-size:15px;font-weight:500}
  .avatar{top:57px;left:87px;width:76px;height:76px;border-radius:50%;border:2px solid var(--avatar-ring);
    background:radial-gradient(circle at 50% 40%,#8a6a52,#3c4a34 70%)}
  .avatar__edit{top:120px;left:145px;width:12px;height:12px;border-radius:50%;background:#fff;border:1px solid var(--avatar-ring)}
  .row{left:21px;width:209px;background:#fff;font-size:7.5px;display:flex;align-items:center;padding:0 8px;gap:6px}
  .row .edit{margin-left:auto}
  .row--links{align-items:flex-start;padding-top:9px}
  .links{line-height:15px}
  .links .add{color:#888}

  /* Main */
  .menu{top:22px;left:14px;width:20px;height:16px;background:var(--ice);display:flex;align-items:center;justify-content:center}
  .main__title{top:24px;left:95px;font-size:11px;font-weight:500}
  .main__points{top:24px;right:12px;font-size:11px;font-weight:500}
  .canvas-area{top:64px;left:14px;width:226px;height:171px;background:var(--pale);border-radius:8px}
  .pencil{top:76px;left:30px}
  .btn-outline{top:267px;height:21px;font-size:7px;display:flex;align-items:center;justify-content:center}
  .btn-outline--muted{left:35px;width:87px;border:1px solid var(--line);color:#888}
  .btn-outline--accent{left:131px;width:87px;border:1.5px solid var(--navy);color:var(--navy)}
  .word{width:65px;height:40px;background:#fff;border-radius:4px;box-shadow:0 1px 4px rgba(0,0,0,.15);
    font-size:8.5px;display:flex;align-items:center;justify-content:center}
  .word--more{background:#efefef}
  .doodle{top:372px;left:180px;width:34px;height:40px;border-radius:8px;background:var(--ice)}
  .btn-results{top:432px;left:24px;width:205px;height:24px;background:var(--ocean);color:#fff;
    font-size:8.5px;font-weight:500;display:flex;align-items:center;justify-content:center}
</style>
</head>
<body>

<section class="screen screen--signup">
  <div class="abs brand"><div class="brand__name">Brivonest</div><div class="brand__tag">Learn letters and words</div></div>
  <div class="abs hero" role="img" aria-label="Illustration of three children at a chalkboard with multiplication questions"></div>
  <h1 class="abs signup__title">Create an account</h1>
  <p class="abs signup__lead">Enter your email to sign up for this app</p>
  <div class="abs field"><span>email@domain.com</span>
    <svg width="8" height="6" viewBox="0 0 8 6"><rect width="8" height="6" fill="#999"/><path d="M0 0l4 3 4-3" stroke="#fff" fill="none" stroke-width=".8"/></svg></div>
  <div class="abs btn-primary">Sign up with email</div>
  <div class="abs divider">or continue with</div>
  <div class="abs btn-soft"><span class="dot"></span>Quarnix</div>
  <p class="abs legal">By clicking continue, you agree to our <b>Terms of Service</b><br>and <b>Privacy Policy</b></p>
</section>

<section class="screen screen--profile">
  <div class="abs back"><svg width="10" height="8" viewBox="0 0 10 8"><path d="M9 4H1M4 1L1 4l3 3" stroke="#111" stroke-width="1.3" fill="none"/></svg></div>
  <h1 class="abs screen-title">Profile</h1>
  <div class="abs avatar" role="img" aria-label="Profile photo of the user"></div>
  <div class="abs avatar__edit"></div>

  <div class="abs row" style="top:156px;height:24px">
    <svg width="8" height="8" viewBox="0 0 8 8"><circle cx="4" cy="2.5" r="1.8" fill="none" stroke="#555" stroke-width=".7"/><path d="M.8 8a3.2 3 0 016.4 0" fill="none" stroke="#555" stroke-width=".7"/></svg>
    Mara Lindell<svg class="edit" width="9" height="9" viewBox="0 0 9 9"><rect x=".5" y="1.5" width="7" height="7" fill="none" stroke="#222" stroke-width=".8"/><path d="M3.5 5.5l5-5" stroke="#222" stroke-width="1.2"/></svg></div>
  <div class="abs row" style="top:195px;height:25px">
    <svg width="8" height="8" viewBox="0 0 8 8"><circle cx="4" cy="4" r="3.5" fill="none" stroke="#555" stroke-width=".7"/><path d="M4 3.5v2.5" stroke="#555" stroke-width=".7"/></svg>
    @username<svg class="edit" width="9" height="9" viewBox="0 0 9 9"><rect x=".5" y="1.5" width="7" height="7" fill="none" stroke="#222" stroke-width=".8"/><path d="M3.5 5.5l5-5" stroke="#222" stroke-width="1.2"/></svg></div>
  <div class="abs row" style="top:234px;height:24px">
    <svg width="8" height="6" viewBox="0 0 8 6"><rect width="8" height="6" fill="#222"/><path d="M0 0l4 3 4-3" stroke="#fff" fill="none" stroke-width=".8"/></svg>
    name@domain.com<svg class="edit" width="9" height="9" viewBox="0 0 9 9"><rect x=".5" y="1.5" width="7" height="7" fill="none" stroke="#222" stroke-width=".8"/><path d="M3.5 5.5l5-5" stroke="#222" stroke-width="1.2"/></svg></div>
  <div class="abs row row--links" style="top:272px;height:85px">
    <svg width="9" height="9" viewBox="0 0 9 9"><path d="M3.5 5.5l2-2M2.5 4.5l-1 1a1.4 1.4 0 002 2l1-1M6.5 4.5l1-1a1.4 1.4 0 00-2-2l-1 1" fill="none" stroke="#333" stroke-width=".8"/></svg>
    <div class="links">website.net<br>mylink.net<br>yourlink.net<br><span class="add">+ Add Link</span></div>
    <svg class="edit" width="9" height="9" viewBox="0 0 9 9"><rect x=".5" y="1.5" width="7" height="7" fill="none" stroke="#222" stroke-width=".8"/><path d="M3.5 5.5l5-5" stroke="#222" stroke-width="1.2"/></svg></div>
  <div class="abs row" style="top:372px;height:25px">
    <svg width="8" height="8" viewBox="0 0 8 8"><circle cx="4" cy="2.5" r="1.8" fill="none" stroke="#555" stroke-width=".7"/><path d="M.8 8a3.2 3 0 016.4 0" fill="none" stroke="#555" stroke-width=".7"/></svg>
    A description of this user.<svg class="edit" width="9" height="9" viewBox="0 0 9 9"><rect x=".5" y="1.5" width="7" height="7" fill="none" stroke="#222" stroke-width=".8"/><path d="M3.5 5.5l5-5" stroke="#222" stroke-width="1.2"/></svg></div>
</section>

<section class="screen screen--main">
  <div class="abs menu"><svg width="10" height="8" viewBox="0 0 10 8"><path d="M0 1h10M0 4h10M0 7h10" stroke="#555" stroke-width="1"/></svg></div>
  <h1 class="abs main__title">Main Screen</h1>
  <div class="abs main__points">16 Points</div>
  <div class="abs canvas-area" aria-label="Drawing area"></div>
  <svg class="abs pencil" width="9" height="9" viewBox="0 0 9 9"><path d="M1 8l1-3 5-5 2 2-5 5z" fill="#111"/></svg>
  <div class="abs btn-outline btn-outline--muted">Show all Words</div>
  <div class="abs btn-outline btn-outline--accent">Play all words</div>
  <div class="abs word" style="top:308px;left:14px">Word A</div>
  <div class="abs word" style="top:308px;left:94px">Word B</div>
  <div class="abs word" style="top:308px;left:174px">Word C</div>
  <div class="abs word" style="top:364px;left:14px">Word D</div>
  <div class="abs word word--more" style="top:364px;left:94px">···</div>
  <div class="abs doodle" role="img" aria-label="Sketch of a paper plane with a looping trail"></div>
  <div class="abs btn-results">Show me the results</div>
</section>

</body>
</html>
```